Brindovalle Business cards

Dear team, I need to get the design file to suit it to our team. The focus of the business card is the Automotive Market and the design must be in black colour and the logo must be in glossy black. On the front of the card I need to get the following info:

- Name and Surname
- Title
- eMail
- Phone Number
- Skype account
- domain address

```html
<!DOCTYPE html>
<html lang="en">
<head>
<meta charset="utf-8">
<title>Brindovalle Business Cards</title>
<link rel="stylesheet" href="https://fonts.googleapis.com/css2?family=Archivo:wght@400;600;800&display=swap">
<style>
  :root {
    --page: #d9d9db;
    --card: #1c1c1d;
    --gloss-dark: #0e0e0f;
    --gloss-light: #3a3a3c;
    --accent: #e3242b;
    --text: #ffffff;
    --text-soft: #e6e6e6;
  }
  * { margin: 0; padding: 0; box-sizing: border-box; }
  html, body {
    width: 1200px; height: 912px; overflow: hidden;
    background: var(--page);
    font-family: "Archivo", Arial, sans-serif;
  }
  .canvas { position: relative; width: 1200px; height: 912px; }
  .card {
    position: absolute; left: 290px; width: 620px; height: 354px;
    background: var(--card);
    box-shadow: 0 10px 30px rgba(0,0,0,.25);
    overflow: hidden;
  }
  .card--back { top: 84px; }
  .card--front { top: 474px; }

  /* back side */
  .back-pattern {
    position: absolute; inset: 0;
    background: linear-gradient(160deg, var(--gloss-light) 0%, var(--gloss-dark) 55%, #000 100%);
  }
  .back-mark {
    position: absolute; right: 112px; top: 96px;
    display: flex; align-items: center; gap: 10px;
  }
  .back-mark__square { width: 34px; height: 34px; background: var(--accent); }
  .back-mark__name { font-weight: 800; font-size: 20px; color: var(--text); }

  /* front side */
  .wordmark {
    position: absolute; left: 40px; top: 176px;
    display: flex; align-items: center; gap: 10px;
    white-space: nowrap;
  }
  .wordmark__square { width: 28px; height: 28px; background: var(--accent); flex: none; }
  .wordmark__name {
    font-weight: 800; font-size: 31px; letter-spacing: -0.5px; color: var(--text);
  }
  .wordmark__tld { font-size: 15px; letter-spacing: 0; }
  .divider {
    position: absolute; left: 392px; top: 84px;
    width: 2px; height: 122px; background: var(--accent);
  }
  .contact {
    position: absolute; left: 410px; top: 80px; color: var(--text-soft);
    white-space: nowrap;
  }
  .contact__name {
    font-weight: 800; font-size: 21px; color: var(--accent);
    text-transform: uppercase; letter-spacing: .3px; line-height: 1.05;
  }
  .contact__title { font-size: 14px; margin: 2px 0 10px; }
  .contact__list { list-style: none; font-size: 14px; line-height: 1.45; }
  .contact__list li { display: flex; align-items: center; gap: 6px; }
  .contact__list svg { width: 11px; height: 11px; flex: none; }
  .address {
    position: absolute; left: 200px; bottom: 44px;
    font-size: 15px; color: var(--text); white-space: nowrap;
  }
</style>
</head>
<body>
<main class="canvas">

  <section class="card card--back" aria-label="Card back">
    <div class="back-pattern" role="img" aria-label="Glossy black tonal pattern of repeated brand symbols"></div>
    <div class="back-mark">
      <span class="back-mark__square"></span>
      <span class="back-mark__name">Brindovalle</span>
    </div>
  </section>

  <section class="card card--front" aria-label="Card front">
    <div class="wordmark">
      <span class="wordmark__square"></span>
      <span class="wordmark__name">Brindovalle<span class="wordmark__tld">.com</span></span>
    </div>

    <div class="divider"></div>

    <div class="contact">
      <p class="contact__name">Marco Delvan</p>
      <p class="contact__title">Director</p>
      <ul class="contact__list">
        <li>
          <svg viewBox="0 0 12 12"><path fill="#e3242b" d="M2.5 1h2l1 2.6-1.3 1a6 6 0 0 0 3.2 3.2l1-1.3L11 7.5v2c0 .8-.7 1.5-1.5 1.5A8.5 8.5 0 0 1 1 2.5C1 1.7 1.7 1 2.5 1z"/></svg>
          555-014-2230
        </li>
        <li>
          <svg viewBox="0 0 12 12"><rect x="0.5" y="2.5" width="11" height="7.5" fill="#e3242b"/><path d="M1 3l5 4 5-4" stroke="#1c1c1d" stroke-width="1" fill="none"/></svg>
          info@brindovalle.com
        </li>
        <li>
          <svg viewBox="0 0 12 12"><circle cx="6" cy="6" r="5.5" fill="#e3242b"/></svg>
          brindovalle
        </li>
      </ul>
    </div>

    <p class="address">2840 W Larkspur Ave, Fairhaven, Ohio 44210</p>
  </section>

</main>
</body>
</html>
```